Homemaking training schools needs a Business Card design

Designer, Hello!

No special requirements, good-looking enough.
--------------------------------------------------------------------------

Name: Marcus Dole
Chairman
Tel: 0574-71948263
Mobile: 13857420916
Email: kelvora@mailnest.example
Web: www.prt2019.example
Add: No.258, LanpingJie, BeiyuanQu, Ningbo, Zhejiang

LOGO
Ningbo PRT Homemaking Training School

Target Market(s)

pregnant women, mothers, infants, the elderly and families, including cleaning, cooking, nursing training.

Industry/Entity Type

Business

Contact Information for Business Card

Name: Marcus Dole
Chairman
Tel: 0574-71948263
Mobile: 13857420916
Email: kelvora@mailnest.example
Web: www.prt2019.example

LOGO

Font styles to use
Serif
Sans Serif
Decorative

Requirements
Nice to have
• Feels: clean, specifications, safety, comfort, warmth and happiness.

```html
<!DOCTYPE html>
<html lang="en">
<head>
<meta charset="utf-8">
<title>PuRuiTang Business Card</title>
<link rel="stylesheet" href="https://fonts.googleapis.com/css2?family=Open+Sans:wght@400;600;700&display=swap">
<style>
  :root {
    --brand-blue: #2b8fd4;
    --band-blue: #2f96d8;
    --ink: #3c3c3c;
    --ink-soft: #5a5a5a;
    --paper: #fbfbf9;
    --backdrop: #e9e7e3;
  }
  * { box-sizing: border-box; margin: 0; padding: 0; }
  html, body {
    width: 1200px; height: 987px; overflow: hidden;
    background: var(--backdrop);
    font-family: "Open Sans", Arial, sans-serif;
    color: var(--ink);
  }
  .canvas {
    width: 1200px; height: 987px;
    display: flex; flex-direction: column; align-items: center; justify-content: center;
    gap: 40px;
  }
  .card {
    position: relative;
    width: 700px; height: 420px;
    background: var(--paper);
    box-shadow: 0 6px 18px rgba(0,0,0,.12);
    overflow: hidden;
  }
  .card-back { border-bottom: 6px solid var(--brand-blue); }

  /* wordmark placeholder: invented name only, one colour, one weight */
  .brand-name {
    font-weight: 700; color: var(--brand-blue); line-height: 1; white-space: nowrap;
  }

  /* back side */
  .card-back .brand-name {
    position: absolute; left: 0; right: 0; top: 140px;
    text-align: center; font-size: 60px;
  }
  .back-web {
    position: absolute; left: 0; right: 0; top: 300px;
    text-align: center; font-size: 17px; letter-spacing: 8px; color: var(--ink-soft);
  }

  /* front side */
  .card-front .brand-name {
    position: absolute; left: 48px; top: 80px; font-size: 40px;
  }
  .name-band {
    position: absolute; left: 0; right: 0; top: 158px; height: 74px;
    background: var(--band-blue); color: #fff; padding: 10px 0 0 48px;
  }
  .person-name { font-size: 26px; font-weight: 600; line-height: 1.2; }
  .person-title { font-size: 15px; }
  .contact-list {
    position: absolute; left: 48px; top: 262px; list-style: none;
    font-size: 17px; color: var(--ink);
  }
  .contact-list li { display: flex; align-items: center; gap: 12px; height: 34px; }
  .contact-list svg { width: 18px; height: 18px; fill: var(--brand-blue); flex: none; }
  .address {
    position: absolute; right: 44px; bottom: 40px; text-align: right;
    font-size: 17px; line-height: 1.55; color: var(--ink); font-style: normal;
  }
</style>
</head>
<body>
<main class="canvas">
  <section class="card card-back" aria-label="Business card back">
    <p class="brand-name">PuRuiTang</p>
    <p class="back-web">www.prt2019.example</p>
  </section>

  <section class="card card-front" aria-label="Business card front">
    <p class="brand-name">PuRuiTang</p>

    <div class="name-band">
      <p class="person-name">Marcus Dole</p>
      <p class="person-title">Chairman</p>
    </div>

    <ul class="contact-list">
      <li>
        <svg viewBox="0 0 24 24" aria-hidden="true"><path d="M6.6 10.8a15.1 15.1 0 0 0 6.6 6.6l2.2-2.2a1 1 0 0 1 1-.25 11.4 11.4 0 0 0 3.6.57 1 1 0 0 1 1 1V20a1 1 0 0 1-1 1A17 17 0 0 1 3 4a1 1 0 0 1 1-1h3.5a1 1 0 0 1 1 1c0 1.25.2 2.45.57 3.57a1 1 0 0 1-.25 1z"/></svg>
        <span>0574-71948263</span>
      </li>
      <li>
        <svg viewBox="0 0 24 24" aria-hidden="true"><path d="M7 2h10a2 2 0 0 1 2 2v16a2 2 0 0 1-2 2H7a2 2 0 0 1-2-2V4a2 2 0 0 1 2-2zm0 3v13h10V5zm5 14.2a1 1 0 1 0 0 2 1 1 0 0 0 0-2z"/></svg>
        <span>13857420916</span>
      </li>
      <li>
        <svg viewBox="0 0 24 24" aria-hidden="true"><path d="M3 5h18a1 1 0 0 1 1 1v12a1 1 0 0 1-1 1H3a1 1 0 0 1-1-1V6a1 1 0 0 1 1-1zm1 2.3V17h16V7.3l-8 5.2z M4.6 7l7.4 4.8L19.4 7z"/></svg>
        <span>kelvora@mailnest.example</span>
      </li>
    </ul>

    <address class="address">
      No.258, LanpingJie<br>
      BeiyuanQu, Ningbo, Zhejiang<br>
      www.prt2019.example
    </address>
  </section>
</main>
</body>
</html>
```